Design a label for a dog shampoo names fluffo, the sell point of this series of shampoo is “just like wash your dogs with milk, not harm for your hand ”, the style could be gentle or professional or even amazing.

Use only 2 colors in the design job, the color of our logo could be changed, it depends on your whole page. Please design in CDR or ai.

update:
Pls do more change with the fonts when you design the front page, including title and details. Try more styles of fonts. Addition, this design will be printed on the bottle, no a label stick on it.
Updates

Do not put a real dog or animal on the page, Pay more attention to the types of fonts

Reason: Expect for more design idea.

Target Market(s)

people 20-30 years old who have dogs and cats at home

Industry/Entity Type

It Professional

Requirements
Nice to have
• It would be nice if you add some detail words in the design of the right side.

```html
<!DOCTYPE html>
<html lang="en">
<head>
<meta charset="utf-8">
<title>fluffo — super conditioning nutrient shampoo</title>
<link rel="stylesheet" href="https://fonts.googleapis.com/css2?family=Fredoka:wght@600&family=Quicksand:wght@400&display=swap">
<style>
  :root {
    --ink-blue: #0b5aa3;
    --milk-blue: #b9d9ef;
    --paper: #ffffff;
  }
  * { margin: 0; padding: 0; box-sizing: border-box; }
  html, body {
    width: 1200px;
    height: 2297px;
    overflow: hidden;
    background: var(--paper);
  }
  .bottle-print {
    position: relative;
    width: 1200px;
    height: 2297px;
    background: var(--paper);
  }
  .brand-name {
    position: absolute;
    font-family: "Fredoka", "Baloo 2", sans-serif;
    font-weight: 600;
    color: var(--ink-blue);
    line-height: 1;
    white-space: nowrap;
  }
  .brand-name--top {
    left: 92px;
    top: 470px;
    width: 1000px;
    font-size: 440px;
    letter-spacing: 4px;
    text-align: center;
  }
  .brand-name--bottom {
    right: 117px;
    top: 960px;
    font-size: 400px;
    letter-spacing: 6px;
  }
  .selling-points {
    position: absolute;
    right: 670px;
    top: 1052px;
    list-style: none;
    text-align: right;
    font-family: "Fredoka", sans-serif;
    font-weight: 600;
    font-size: 54px;
    letter-spacing: 3px;
    color: var(--ink-blue);
    line-height: 100px;
    font-style: italic;
  }
  .claim-band {
    position: absolute;
    left: 100px;
    top: 1440px;
    width: 995px;
    height: 340px;
  }
  .claim-band svg {
    position: absolute;
    inset: 0;
    width: 100%;
    height: 100%;
  }
  .claim-band__text {
    position: absolute;
    inset: 0;
    display: flex;
    flex-direction: column;
    justify-content: center;
    align-items: center;
    font-family: "Quicksand", sans-serif;
    font-weight: 400;
    font-style: italic;
    font-size: 66px;
    letter-spacing: 20px;
    color: var(--paper);
    line-height: 100px;
  }
</style>
</head>
<body>
<main class="bottle-print">
  <h1 class="brand-name brand-name--top">fluf</h1>
  <span class="brand-name brand-name--bottom" aria-hidden="true">fo</span>

  <ul class="selling-points">
    <li>moisture rich</li>
    <li>smooth &amp; silky</li>
    <li>100ml</li>
  </ul>

  <section class="claim-band">
    <svg viewBox="0 0 995 340" preserveAspectRatio="none" aria-hidden="true">
      <path fill="var(--milk-blue)" d="M40 40 C90 10 160 30 230 22 C300 12 360 30 430 18 C500 6 570 28 640 16 C720 4 800 26 870 14 C930 6 975 30 972 80 C968 120 995 150 985 200 C975 240 992 280 960 305 C920 335 860 318 800 326 C730 336 660 320 590 330 C520 340 450 322 380 332 C310 342 240 322 170 330 C100 338 40 330 18 290 C0 255 14 220 6 180 C-2 140 12 110 8 85 C4 60 18 50 40 40 Z"/>
    </svg>
    <p class="claim-band__text">
      <span>super conditioning</span>
      <span>nutrient shampoo</span>
    </p>
  </section>
</main>
</body>
</html>
```